Label design for organic saffron, saffron and herbal syrup

We cultivate saffron, Damszen roses, flowers and herbs. We would need a recognizable outfit (label) for our products. Theoretically (and practically) we have "converted" the family coat of arms into a kind of LOGO. I would send this in the attachment. It would be nice if - in one way or another - this LOGO / coat of arms could be used (certainly with other colors). For some time we have played with the idea of changing the second part of the family name "Wallmoser" (in German .... greuth sounds similar to Kraut / herb [English]) .... eg Wallmoser's saffron syrup into the labeling.
Our products are primarily syrups, currently herbal syrup and saffron syrup. Here the first problem arises, the only bottles / caps that are actually approved for syrup filling (hot filling) are appallingly ugly (see attachment), the only possibility of "sprucing up" is to use so-called "shrink sleeves" (here we need a diameter of 31 and a length of about 40), the colors of which are also limited. Besides the syrup, we sell saffron as a spice and various herbal mixtures (see appendix current packaging saffron). Our quantities are small (syrup 200ml-330ml), saffron in the gram range.
We also need quasi the back of the labeling (this should be able to be redefined per charge) .... Batch 1 (with small quantity has eg more of herb xy than the next batch or the saffron syrup with batch xy needs more / less saffron). In addition, we are certified organic (for this reason, the reverse side would also have to contain all the requirements of organic labeling) [see attachment].
We do not really want to address a specific clientele. Maybe just people who want to taste, enjoy, mix drinks, cook .... (and - unfortunately - don't like Corvel syrup :-) and want to pay a bit more, or find our saffron or herbs better than others) .
In summary
- Strong recognition value (possibly inclusion of "coat of arms", color variable ... although I personally don't like yellow that much)
- Saffron syrup (the color of the saffron syrup is yellow / golden-yellow-light orange, in a transparent ugly bottle)
- Herbal syrup (color variable from blue / green / brown / red elements, in transparent ugly bottle)
Saffron and other herbs (very small containers, type of container not yet fixed)
Regarding a potential "style" I can unfortunately give little information. On the one hand, I am in love with minimalism, on the other hand, I find the translucent, cryptic, implied enormously attractive and sometimes even the "overloaded" colorful has its charm. I think that all in all, it just has to be coherent, and then it will be good.
Requirements
Must have
- Integration of Code of Arms, modifiable for different products

```html
<!DOCTYPE html>
<html lang="en">
<head>
<meta charset="utf-8">
<title>Wallmoser Herbal Sirup Label</title>
<link rel="stylesheet" href="https://fonts.googleapis.com/css2?family=Open+Sans:wght@700;800&family=Playfair+Display:wght@700&display=swap">
<style>
  :root {
    --page: #ffffff;
    --cream: #fdf0cc;
    --forest: #0d4526;
    --forest-deep: #093519;
    --gold: #c9a24a;
    --gold-light: #f0d98a;
    --gold-dark: #9a7526;
    --navy: #2c2a6e;
    --ink: #2b2b2b;
    --badge-green: #cfe6a8;
    --badge-edge: #5aa332;
  }
  * { box-sizing: border-box; margin: 0; padding: 0; }
  html, body { width: 878px; height: 1200px; overflow: hidden; background: var(--page); }
  .label {
    position: relative;
    width: 878px;
    height: 1200px;
    background: var(--page);
  }
  .label__panel {
    position: absolute;
    left: 49px; top: 48px;
    width: 780px; height: 1099px;
    background: var(--cream);
  }
  .label__shapes {
    position: absolute;
    left: 0; top: 0;
    width: 878px; height: 1200px;
  }
  .brand-name {
    position: absolute;
    left: 239px; top: 318px;
    width: 400px;
    text-align: center;
    font-family: "Playfair Display", Georgia, serif;
    font-weight: 700;
    font-size: 44px;
    color: var(--navy);
    letter-spacing: 0.5px;
  }
  .product-title {
    position: absolute;
    left: 270px; top: 560px;
    width: 333px;
    text-align: center;
    font-family: "Playfair Display", Georgia, serif;
    font-weight: 700;
    font-size: 68px;
    line-height: 72px;
    color: #ffffff;
    text-shadow: 2px 3px 3px rgba(0,0,0,0.75);
  }
  .side-text {
    position: absolute;
    font-family: "Open Sans", Arial, sans-serif;
    font-weight: 800;
    color: var(--ink);
    writing-mode: vertical-rl;
    transform: rotate(180deg);
  }
  .ingredients {
    left: 78px; top: 482px;
    width: 92px; height: 636px;
    font-size: 13.4px;
    line-height: 18.5px;
    text-align: center;
    letter-spacing: 0.3px;
  }
  .maker {
    left: 712px; top: 494px;
    width: 62px; height: 392px;
    font-size: 13.2px;
    line-height: 18px;
    text-align: start;
  }
  .maker__organic { margin-left: 10px; }
  .best-before {
    position: absolute;
    left: 704px; top: 896px;
    width: 90px; height: 206px;
    background: #ffffff;
    border: 1.5px solid #1e1e1e;
  }
  .best-before__label {
    position: absolute;
    left: 6px; bottom: 12px;
    font-family: "Open Sans", Arial, sans-serif;
    font-weight: 800;
    font-size: 17px;
    color: #1e1e1e;
    writing-mode: vertical-rl;
    transform: rotate(180deg);
  }
  .volume, .ratio {
    position: absolute;
    top: 1085px;
    font-family: "Open Sans", Arial, sans-serif;
    font-weight: 700;
    font-size: 23px;
    color: var(--ink);
    transform: scaleX(0.88);
    transform-origin: left top;
  }
  .volume { left: 289px; }
  .ratio { left: 511px; }
</style>
</head>
<body>
<main class="label">
  <div class="label__panel"></div>

  <svg class="label__shapes" viewBox="0 0 878 1200" xmlns="http://www.w3.org/2000/svg">
    <defs>
      <linearGradient id="ornament-tone" x1="0" y1="0" x2="1" y2="1">
        <stop offset="0" stop-color="#0e4a29"/>
        <stop offset="0.5" stop-color="#16583a"/>
        <stop offset="1" stop-color="#0b3f22"/>
      </linearGradient>
      <linearGradient id="gold-band" x1="0" y1="0" x2="0" y2="1">
        <stop offset="0" stop-color="#8e6b22"/>
        <stop offset="0.35" stop-color="#e8c870"/>
        <stop offset="0.6" stop-color="#f3dc92"/>
        <stop offset="1" stop-color="#a57d2c"/>
      </linearGradient>
      <linearGradient id="arch-tone" x1="0" y1="0" x2="0" y2="1">
        <stop offset="0" stop-color="#0f4a29"/>
        <stop offset="1" stop-color="#0a3c20"/>
      </linearGradient>
      <clipPath id="header-clip">
        <rect x="49" y="48" width="780" height="377"/>
      </clipPath>
    </defs>

    <g class="header-ornament" role="img" aria-label="Green ground with gold mandala ornaments on both sides of the crest">
      <rect x="49" y="48" width="780" height="377" fill="url(#ornament-tone)"/>
    </g>

    <g class="crest-window" clip-path="url(#header-clip)">
      <rect x="375" y="40" width="128" height="250" fill="#ffffff"/>
      <circle cx="439" cy="292" r="204" fill="#ffffff" stroke="var(--gold)" stroke-width="3"/>
      <line x1="375" y1="48" x2="375" y2="98" stroke="var(--gold)" stroke-width="3"/>
      <line x1="503" y1="48" x2="503" y2="98" stroke="var(--gold)" stroke-width="3"/>
      <rect x="376.5" y="40" width="125" height="100" fill="#ffffff"/>
    </g>

    <rect class="gold-band" x="49" y="424" width="780" height="34" fill="url(#gold-band)"/>

    <path class="title-arch" role="img" aria-label="Green arch with a faint herb blossom illustration"
          d="M270 458 V738 A166.5 166.5 0 0 0 603 738 V458 Z"
          fill="url(#arch-tone)" stroke="var(--gold)" stroke-width="3"/>

    <g class="organic-badge" role="img" aria-label="Organic certification badge">
      <rect x="393" y="924" width="90" height="187" fill="var(--badge-green)" stroke="var(--badge-edge)" stroke-width="1.5"/>
      <circle cx="438" cy="960" r="24" fill="#ffffff" stroke="#c8202a" stroke-width="3"/>
      <rect x="402" y="1001" width="72" height="48" fill="#7ab648"/>
    </g>
  </svg>

  <div class="brand-name">Wallmoser</div>

  <h1 class="product-title">Herbal<br>Sirup</h1>

  <p class="side-text ingredients">ZUTATEN: Lorem ipsum dolor sit amet, consectetur adipiscing elit. Morbi ultricies molestie orci. Aenean purus mauris, sodales nec diam dignissim, porttitor laoreet enim. Aliquam id sollicitudin turpis. Vivamus aliquet elit sem, et ornare ex aliquam in.</p>

  <div class="side-text maker">
    <p class="maker__organic">*aus kontrolliert biologischer Landwirtschaft</p>
    <p class="maker__address">Expertly crafted by: Halden-Wallmoser<br>1234 Street Name, Any City, District, Country</p>
  </div>

  <div class="best-before">
    <span class="best-before__label">Best Before:</span>
  </div>

  <div class="volume">200mL</div>
  <div class="ratio">1:7</div>
</main>
</body>
</html>
```